Flyer-Design für persönlichen Lauftrainer
Zielgruppe
Die Trabwerk GmbH entwickelt und vertreibt den persönlichen Lauftrainer KOBAL. KOBAL ist ein elektrisch angetriebenes, automatisch gesteuertes Fahrzeug, mithilfe dessen eine Person ein professionell geplantes Lauftraining im Freien absolvieren kann. Das Gerät übernimmt die Trainingssteuerung und fungiert dabei quasi als ein persönlicher Lauftrainer.
Wir sprechen zwei Kundengruppen an:
1. Privatkunden
2. Institutionelle Kunden wie Physiotherapiezentren und -praxen, Sport- und Wellnesshotels, betriebliches Gesundheitsmanagement und Verleihgeschäfte.
Die Gestaltung, Funktionalität und Ausstattung des Geräts spricht jedoch grundsätzlich die Gesamtheit der Läufer und Fun- und Aktivsportler an.
Aufgabenstellung
Für unseren Produktflyer der DINA 4 und beidseitig bedruckt sein soll, suchen wir nach einem sportlichen, kräftigen, dynamischen Design. Das Design sollte für uns im Nachhinein leicht veränderbar sein (Texte, Bilder, etc.), da wir den Flyer für verschiedene geographische Regionen anpassen werden. Hierfür würden wir z.B. Indesign nutzen. Die Texte, die wir Ihnen mitliefern sollten möglichst so übernommen werden. Wenn Sie die Möglichkeit sehen, den Inhalt in anderer Form darzustellen, dann ist das in Ordnung.
Der Text für den Flyer ist folgender:
Slogan zum großen Bild: Sie brauchen einen persönlichen Lauftrainer?
Zu den kleinen Bildern: Schalten Sie KOBAL ein, wählen Sie ihr Trainingsprogramm und es kann los gehen!
Call to Action: Besuchen Sie www.trabwerk-beispiel.com
Adresse:
Trabwerk GmbH
www.trabwerk-beispiel.com
Text für Flyer:
Ihr Problem
⁃ Sie haben einen vollen Arbeitstag und wollen trotzdem endlich Ihre Fitness verbessern?
⁃ Sie möchten dringend an Ihrer Figur und Ihrem Gewicht arbeiten?
⁃ Sie wollen schon lange an Ihrem ersten 10 Kilometerlauf teilnehmen und sich optimal darauf vorbereiten?
⁃ Sie möchten einen Trainer haben, der Ihnen jederzeit zur Verfügung steht?
⁃ Mit Ihrer Pulsuhr und Ihrer Lauf-App machen Sie nur geringe oder gar keine Trainingsfortschritte?
Unsere Lösung KOBAL Ihr persönlicher Lauftrainer
⁃ bietet Ihnen ein optimales Lauftraining im Freien durch eine kontrollierte, direkte Geschwindigkeitsvorgabe,
⁃ alarmiert Sie nicht nur wenn Sie etwas falsch machen (indirektes Feedback), er zeigt Ihnen wie Sie es richtig machen (direktes Feedback),
⁃ führt dabei Trainingsprogramme aus, die auf Ihre individuellen Fitness- und Leistungsziele zugeschnitten sind,
⁃ verhindert, dass Sie sich beim Training überlasten,
⁃ unterstützt Sie als
⁃ Anfänger beim Trainingseinstieg
⁃ Fortgeschrittene beim Aufba..

```html
<!DOCTYPE html>
<html lang="de">
<head>
<meta charset="utf-8">
<title>Trabwerk – KOBAL Flyer</title>
<link rel="stylesheet" href="https://fonts.googleapis.com/css2?family=Teko:wght@500;600&family=Bitter:ital,wght@0,400;0,600;0,700;1,400;1,700&display=swap">
<style>
  :root {
    --orange: #f08a2c;
    --orange-soft: #f3a24f;
    --orange-red: #e8561c;
    --ink: #2b2b2b;
    --text: #5a5650;
    --paper: #ffffff;
    --paper-warm: #f1eee9;
    --stage: #34373c;
    --black: #111111;
    --head: "Teko", "Oswald", sans-serif;
    --serif: "Bitter", Georgia, serif;
  }
  * { margin: 0; padding: 0; box-sizing: border-box; }
  html, body { width: 1200px; height: 831px; overflow: hidden; background: var(--stage); }
  .page { position: absolute; top: 35px; width: 538px; height: 760px; background: var(--paper); overflow: hidden; }
  .page--front { left: 42px; }
  .page--back { left: 620px; background: var(--paper-warm); }
  .layer { position: absolute; left: 0; top: 0; width: 538px; height: 760px; }
  .abs { position: absolute; }

  /* front */
  .front-kicker { left: 82px; top: 50px; font: 600 17px/1 var(--serif); color: var(--ink); letter-spacing: .5px; }
  .front-title { left: 81px; top: 74px; font: 600 44px/36px var(--head); color: var(--orange); letter-spacing: 1px; }
  .cta-label { left: 37px; top: 614px; font: 600 20px/1 var(--head); color: var(--orange); letter-spacing: .5px; }
  .cta-url { left: 37px; top: 636px; font: 600 15px/1 var(--serif); color: var(--ink); letter-spacing: .4px; }
  .brand { display: flex; align-items: center; gap: 8px; font: 700 38px/1 var(--serif); color: var(--orange); }
  .brand__dot { width: 30px; height: 30px; border-radius: 50%; background: var(--orange); }
  .front-brand { right: 36px; top: 688px; }

  /* back */
  .section-title { font: 600 20px/1 var(--head); color: var(--orange); letter-spacing: .6px; }
  .problem-title { left: 24px; top: 28px; }
  .solution-title { left: 233px; top: 28px; }
  .list { list-style: none; font: 400 9.4px/11.6px var(--serif); color: var(--text); }
  .list li { position: relative; padding-left: 14px; margin-bottom: 4px; }
  .list li::before { content: "•"; position: absolute; left: 0; top: 0; }
  .list em { font-style: italic; font-weight: 700; color: #4a463f; }
  .list i { font-style: italic; }
  .problem-list { left: 24px; top: 52px; width: 200px; }
  .solution-sub { left: 233px; top: 50px; font: 600 10px/1 var(--serif); color: var(--orange-red); }
  .solution-list { left: 233px; top: 64px; width: 202px; }
  .ready-head { left: 385px; top: 314px; font: 500 11px/1 var(--head); color: #fff; letter-spacing: .5px; }
  .ready-text { left: 385px; top: 333px; width: 140px; font: 400 9.4px/12.8px var(--serif); color: #fff; }
  .how-title { left: 139px; top: 448px; }
  .how-body { left: 139px; top: 476px; width: 270px; }
  .how-body__clear { float: right; width: 46px; height: 98px; }
  .how-list { position: static; font-size: 7.6px; line-height: 10.6px; }
  .how-list li { padding-left: 6px; margin-bottom: 3px; }
  .badge { left: 368px; top: 397px; width: 170px; height: 170px; border-radius: 50%; background: var(--black);
           display: flex; flex-direction: column; align-items: center; justify-content: center; text-align: center;
           transform: rotate(-6deg); font-family: var(--head); }
  .badge__head { color: var(--orange); font-weight: 600; font-size: 11px; letter-spacing: .4px; margin-bottom: 8px; }
  .badge__item { color: #fff; font-weight: 500; font-size: 10.5px; line-height: 11px; letter-spacing: .4px; margin-bottom: 8px; }
  .back-brand { left: 315px; top: 712px; font-size: 22px; gap: 5px; }
  .back-brand .brand__dot { width: 17px; height: 17px; }
  .imprint { left: 432px; top: 675px; font: 700 6.6px/8.4px var(--serif); font-style: normal; color: var(--ink); }
  .imprint .gap { height: 6px; }
  .imprint b { color: var(--orange); }
</style>
</head>
<body>

<section class="page page--front">
  <svg class="layer" viewBox="0 0 538 760" aria-hidden="true">
    <defs>
      <linearGradient id="peach" x1="1" y1="0" x2="0.35" y2="0.7">
        <stop offset="0" stop-color="#f7b48c"/>
        <stop offset="1" stop-color="#ffffff"/>
      </linearGradient>
    </defs>
    <rect width="538" height="260" fill="url(#peach)"/>
  </svg>
  <svg class="layer" viewBox="0 0 538 760" role="img" aria-label="Foto: erschöpfter Läufer auf einem Feldweg in sonniger Hügellandschaft">
    <defs>
      <linearGradient id="field" x1="0" y1="0" x2="0" y2="1">
        <stop offset="0" stop-color="#fcf7ea"/>
        <stop offset=".35" stop-color="#e9d9ad"/>
        <stop offset=".6" stop-color="#c9a767"/>
        <stop offset="1" stop-color="#8d7a4e"/>
      </linearGradient>
    </defs>
    <polygon points="0,172 181,218 538,135 538,590 380,640 100,565 0,590" fill="url(#field)"/>
  </svg>
  <svg class="layer" viewBox="0 0 538 760" aria-hidden="true">
    <polygon points="0,590 100,565 380,640 538,590 538,760 0,760" fill="#ffffff"/>
    <polyline points="0,165 181,211 538,128" fill="none" stroke="var(--orange)" stroke-width="5"/>
    <line x1="330" y1="652" x2="538" y2="588" stroke="var(--orange)" stroke-width="3"/>
  </svg>

  <p class="abs front-kicker">SIE BRAUCHEN EINEN</p>
  <h1 class="abs front-title">PERSÖNLICHEN<br>LAUFTRAINER?</h1>
  <p class="abs cta-label">BESUCHEN SIE</p>
  <p class="abs cta-url">WWW.TRABWERK-BEISPIEL.COM</p>
  <div class="abs brand front-brand"><span class="brand__dot"></span>trabwerk</div>
</section>

<section class="page page--back">
  <svg class="layer" viewBox="0 0 538 760" aria-hidden="true">
    <defs>
      <radialGradient id="glow" cx=".6" cy=".2" r=".7">
        <stop offset="0" stop-color="#faf9f6"/>
        <stop offset="1" stop-color="#ebe7e0"/>
      </radialGradient>
    </defs>
    <rect width="538" height="760" fill="url(#glow)"/>
  </svg>

  <svg class="layer" viewBox="0 0 538 760" role="img" aria-label="Produktfoto: grüner KOBAL Lauftrainer mit Lenker und Smartphone-Halterung">
    <defs>
      <linearGradient id="device" x1="0" y1="0" x2="0" y2="1">
        <stop offset="0" stop-color="#eceae5"/>
        <stop offset=".5" stop-color="#7fd36a"/>
        <stop offset="1" stop-color="#3f8f37"/>
      </linearGradient>
    </defs>
    <rect x="438" y="20" width="98" height="250" rx="6" fill="url(#device)" opacity=".85"/>
  </svg>

  <svg class="layer" viewBox="0 0 538 760" role="img" aria-label="Fotoserie: Läuferin schaltet den Lauftrainer ein, wählt ein Programm und läuft los">
    <defs>
      <linearGradient id="strip" x1="0" y1="0" x2="0" y2="1">
        <stop offset="0" stop-color="#a9c46e"/>
        <stop offset=".6" stop-color="#7e8f58"/>
        <stop offset="1" stop-color="#c9b68a"/>
      </linearGradient>
    </defs>
    <polygon points="0,279 80,279 94,342 80,405 0,405" fill="url(#strip)"/>
    <polygon points="88,279 168,279 182,342 168,405 88,405 102,342" fill="url(#strip)"/>
    <polygon points="176,279 256,279 270,342 256,405 176,405 190,342" fill="url(#strip)"/>
    <polygon points="264,279 340,279 354,342 340,405 264,405 278,342" fill="url(#strip)"/>
  </svg>

  <svg class="layer" viewBox="0 0 538 760" role="img" aria-label="Foto: Läuferin joggt hinter dem Lauftrainer im Abendlicht">
    <defs>
      <linearGradient id="dusk" x1="0" y1="0" x2="0" y2="1">
        <stop offset="0" stop-color="#b7b3b8"/>
        <stop offset=".55" stop-color="#6f6a7a"/>
        <stop offset="1" stop-color="#8a7a5c"/>
      </linearGradient>
    </defs>
    <rect x="0" y="416" width="118" height="344" fill="url(#dusk)"/>
  </svg>

  <svg class="layer" viewBox="0 0 538 760" aria-hidden="true">
    <polygon points="344,271 538,271 538,415 344,415 362,343" fill="var(--orange-soft)"/>
    <polygon points="19,760 538,636 538,760" fill="#ffffff"/>
    <line x1="19" y1="760" x2="538" y2="636" stroke="var(--orange)" stroke-width="3"/>
  </svg>

  <h2 class="abs section-title problem-title">IHR PROBLEM</h2>
  <ul class="abs list problem-list">
    <li>Sie haben einen vollen Arbeitstag und wollen trotzdem endlich <em>Ihre Fitness verbessern?</em></li>
    <li>Sie möchten dringend an <em>Ihrer Figur und Ihrem Gewicht</em> arbeiten?</li>
    <li>Sie wollen schon lange an Ihrem ersten <em>10 Kilometerlauf</em> teilnehmen und sich optimal darauf vorbereiten?</li>
    <li>Sie möchten einen Trainer haben, der Ihnen <em>jederzeit zur Verfügung</em> steht?</li>
    <li>Mit Ihrer Pulsuhr und Ihrer Lauf-App machen Sie nur geringe oder gar keine Trainingsfortschritte?</li>
  </ul>

  <h2 class="abs section-title solution-title">UNSERE LÖSUNG</h2>
  <p class="abs solution-sub">KOBAL – Ihr persönlicher Lauftrainer</p>
  <ul class="abs list solution-list">
    <li>bietet Ihnen ein <em>optimales Lauftraining</em> im Freien durch eine kontrollierte, direkte Geschwindigkeitsvorgabe</li>
    <li>alarmiert Sie nicht nur wenn Sie etwas falsch machen <i>(indirektes Feedback)</i>, er <em>zeigt Ihnen wie Sie es richtig machen</em> <i>(direktes Feedback)</i></li>
    <li>führt dabei Trainingsprogramme aus, die auf <em>Ihre individuellen Fitness- und Leistungsziele</em> zugeschnitten sind</li>
    <li>verhindert, dass Sie sich beim <em>Training überlasten</em></li>
  </ul>

  <p class="abs ready-head">KOBAL IST JEDERZEIT VERFÜGBAR.</p>
  <p class="abs ready-text">Sie müssen ihn nur einschalten, Ihr Trainingsprogramm aus-wählen und schon kann es losgehen!</p>

  <h2 class="abs section-title how-title">UND SO FUNKTIONIERT KOBAL</h2>
  <div class="abs how-body">
    <div class="how-body__clear" aria-hidden="true"></div>
    <ul class="list how-list">
      <li>KOBAL ist ein elektrisch angetriebenes Fahrzeug</li>
      <li>das wie ein Tempomacher vor dem Läufer her fährt</li>
      <li>mit einer Geschwindigkeit, die so geregelt ist, dass ein bestimmter Puls erreicht und eingehalten werden kann. Ist Ihr Puls zu hoch wird KOBAL langsamer, ist Ihr Puls zu niedrig, beschleunigt KOBAL.</li>
      <li>Er fährt selbständig und muss weder geschoben noch gelenkt werden. Sie laufen freihändig, wie Sie es gewohnt sind.</li>
      <li>Er führt Programme aus, die Sie wie eine Smartphone App mit wenigen Mausklicks aus dem trabwerk Store herunterladen und installieren können.</li>
      <li>Wie bei einem Laufband sind Sie mit KOBAL über eine Sicherungsleine verbunden. Wird diese Verbindung gelöst, bremst das Gerät sofort ab und bleibt stehen.</li>
    </ul>
  </div>

  <div class="abs badge">
    <p class="badge__head">KOBAL UNTERSTÜTZT SIE ALS</p>
    <p class="badge__item">ANFÄNGER BEIM<br>TRAININGSEINSTIEG</p>
    <p class="badge__item">FORTGESCHRITTENE BEIM<br>AUFBAUTRAINING</p>
    <p class="badge__item">"PROFI" BEI EINER OPTIMALEN<br>WETTKAMPFVORBEREITUNG</p>
  </div>

  <div class="abs brand back-brand"><span class="brand__dot"></span>trabwerk</div>
  <address class="abs imprint">
    Trabwerk GmbH<br>Läuferweg 15<br>D-12345 Musterstadt
    <div class="gap"></div>
    <b>T</b> +49 123 456 789-0<br><b>F</b> +49 123 456 789-9
    <div class="gap"></div>
    info@trabwerk-beispiel.com<br>www.trabwerk-beispiel.com
  </address>
</section>

</body>
</html>
```